Marwick Family Chiropractic Stationary

The letterhead and business card must have our logo.
We would like to see the logo used in different ways ( It can be expanded upon in the stationary.)
Please use the the same or similar colors.
Must be eye catching and memorable.
Must be easy to read

Reason: The doctor has been too busy to make any final decisions. He would like to give himself a little more time.

Target Market(s)

Chiropractic Healthcare

Industry/Entity Type

Business

Requirements
Must have
• Dr. Leonard Marwick D.C.
Chiropractor

860-555-0183

417 Birchfield Road, Suite 3
Hollis Bay, ME 06091

drmarwick@marwickspine.example
www.marwickspine.example
www.socialhub.example/MarwickSpine
Should not have
• should not be difficult to read

```html
<!DOCTYPE html>
<html lang="en">
<head>
<meta charset="utf-8">
<title>Marwick Family Chiropractic Stationery</title>
<link rel="stylesheet" href="https://fonts.googleapis.com/css2?family=Josefin+Sans:wght@600;700&family=Source+Sans+3:wght@400&display=swap">
<style>
  :root {
    --backdrop: #231f20;
    --paper: #ffffff;
    --ink: #231f20;
    --brand-green: #009245;
    --card-lime: #8dc63f;
    --rule-lime: #c8dc2e;
    --rule-green: #9fcc3b;
    --leaf-light: #d7e43a;
    --leaf-olive: #8c8a3e;
    --trunk: #1f1d12;
  }
  * { box-sizing: border-box; margin: 0; padding: 0; }
  html, body { width: 1200px; height: 811px; overflow: hidden; background: var(--backdrop); }
  body { position: relative; font-family: "Josefin Sans", Arial, sans-serif; color: var(--ink); }

  .letterhead { position: absolute; left: 50px; top: 21px; width: 594px; height: 759px; background: var(--paper); }
  .card-front { position: absolute; left: 700px; top: 100px; width: 456px; height: 267px; background: var(--card-lime); }
  .card-back { position: absolute; left: 668px; top: 401px; width: 456px; height: 267px; background: var(--paper); overflow: hidden; }

  .brand-mark { position: absolute; border-radius: 50%; background: var(--brand-green); }
  .brand-name { position: absolute; font-weight: 700; color: var(--brand-green); letter-spacing: 0.5px; line-height: 1; }

  .letterhead .brand-mark { left: 70px; top: 28px; width: 62px; height: 62px; }
  .letterhead .brand-name { left: 52px; top: 103px; font-size: 22px; }
  .letterhead .phone { position: absolute; left: 39px; top: 131px; font-size: 15.5px; font-weight: 700; }
  .letterhead .address { position: absolute; left: 22px; top: 150px; font-size: 9px; font-weight: 700; line-height: 11.5px; }

  .letter-body { position: absolute; left: 75px; width: 466px; font-family: "Source Sans 3", Arial, sans-serif; font-size: 10.4px; line-height: 12.9px; }
  .letter-body.p1 { top: 252px; }
  .letter-body.p2 { top: 337px; }
  .letter-body.p3 { top: 416px; }

  .signature { position: absolute; left: 79px; top: 546px; width: 92px; height: 22px; background: linear-gradient(90deg, #e6e6e6, #f4f4f4); }

  .sender { position: absolute; left: 356px; top: 651px; }
  .name { font-size: 14.6px; font-weight: 700; line-height: 1.1; white-space: nowrap; }
  .title { font-size: 11px; font-weight: 700; padding-left: 65px; margin-top: 2px; }
  .contact { font-size: 10.5px; font-weight: 700; line-height: 14.2px; white-space: nowrap; }
  .sender .contact { margin-top: 9px; }

  .rule { position: absolute; height: 1px; z-index: 2; }
  .rule.top { background: var(--rule-lime); }
  .rule.bottom { background: var(--rule-green); }
  .letterhead .rule { left: 17px; width: 560px; }
  .letterhead .rule.top { top: 739px; }
  .letterhead .rule.bottom { top: 749px; }

  .card-front .brand-mark { left: 183px; top: 40px; width: 90px; height: 90px; }
  .card-front .brand-name { left: 0; width: 456px; text-align: center; top: 185px; font-size: 44px; }

  .card-back .holder { position: absolute; left: 60px; top: 59px; }
  .card-back .title { padding-left: 58px; }
  .card-back .address { position: absolute; left: 60px; top: 110px; font-size: 9px; font-weight: 700; line-height: 11.5px; }
  .card-back .phone { position: absolute; left: 60px; top: 135px; font-size: 15.5px; font-weight: 700; }
  .card-back .contact { position: absolute; left: 60px; top: 157px; }
  .card-back .rule { left: 20px; width: 367px; }
  .card-back .rule.top { top: 236px; }
  .card-back .rule.bottom { top: 245px; }
  .leaf-decor { position: absolute; z-index: 1; left: 315px; top: 9px; width: 141px; height: 258px;
    background: linear-gradient(180deg, var(--leaf-light) 0%, var(--card-lime) 40%, var(--brand-green) 70%, var(--trunk) 100%); opacity: 0.85; }
</style>
</head>
<body>

<section class="letterhead">
  <div class="brand-mark"></div>
  <div class="brand-name">MARWICK</div>
  <div class="phone">860-555-0183</div>
  <div class="address">417 Birchfield Road, Suite 3<br>Hollis Bay, ME 06091</div>

  <p class="letter-body p1">Lorem ipsum dolor sit amet, consectetur adipisicing elit, sed do eiusmod tempor incididunt ut labore et dolore magna aliqua. Ut enim ad minim veniam, quis nostrud exercitation ullamco laboris nisi ut aliquip ex ea commodo consequat. Duis aute irure dolor in reprehenderit in voluptate velit esse cillum dolore eu fugiat nulla pariatur. Excepteur sint occaecat cupidatat non proident, sunt in culpa qui officia deserunt mollit anim id est laborum.</p>
  <p class="letter-body p2">Lorem ipsum dolor sit amet, consectetur adipisicing elit, sed do eiusmod tempor incididunt ut labore et dolore magna aliqua. Ut enim ad minim veniam, quis nostrud exercitation ullamco laboris nisi ut aliquip ex ea commodo consequat. Duis aute irure dolor in reprehenderit in voluptate velit esse cillum dolore eu fugiat nulla pariatur. Excepteur sint occaecat cupidatat non proident, sunt in culpa qui officia deserunt mollit anim id est laborum.</p>
  <p class="letter-body p3">Lorem ipsum dolor sit amet, consectetur adipisicing elit, sed do eiusmod tempor incididunt ut labore et dolore magna aliqua. Ut enim ad minim veniam, quis nostrud exercitation ullamco laboris nisi ut aliquip ex ea commodo consequat. Duis aute irure dolor in reprehenderit in voluptate velit esse cillum dolore eu fugiat nulla pariatur. Excepteur sint occaecat cupidatat non proident, sunt in culpa qui officia deserunt mollit anim id est laborum.</p>

  <div class="signature" role="img" aria-label="Handwritten signature of Dr. Leonard Marwick"></div>

  <div class="sender">
    <div class="name">Dr. Leonard Marwick D.C.</div>
    <div class="title">Chiropractor</div>
    <div class="contact">drmarwick@marwickspine.example<br>www.marwickspine.example<br>www.socialhub.example/MarwickSpine</div>
  </div>

  <div class="rule top"></div>
  <div class="rule bottom"></div>
</section>

<section class="card-front">
  <div class="brand-mark"></div>
  <div class="brand-name">MARWICK</div>
</section>

<section class="card-back">
  <div class="holder">
    <div class="name">Dr. Leonard Marwick D.C.</div>
    <div class="title">Chiropractor</div>
  </div>
  <div class="address">417 Birchfield Road, Suite 3<br>Hollis Bay, ME 06091</div>
  <div class="phone">860-555-0183</div>
  <div class="contact">drmarwick@marwickspine.example<br>www.marwickspine.example<br>www.socialhub.example/MarwickSpine</div>
  <div class="rule top"></div>
  <div class="rule bottom"></div>
  <div class="leaf-decor" role="img" aria-label="Decorative cluster of green and yellow leaves above dark tree trunks on a green hill"></div>
</section>

</body>
</html>
```